Mortgage Company ready to make a statement!

We have a basic logo that I am fairly happy with ... but it could use a little bit of tweaking before we order the sign for our building. We also want some knock-your-socks-off business cards.
Problem: Inside of our Mortgage Office (Bright Fern Mortgage Group), we are going to have a coffee lounge (Sunbrew Cafe) for Realtors to use instead of the local Cuppington to meet with homebuyers. The office and coffee lounge are in an industrial building and is decorated with cozy overstuffed chairs, a hodge podge of interesting lamps and furniture, and goal is to make it as inviting as possible. However, we are a financial institution... so we need to keep it pretty clean as well.
One of my favorite marketing ideas is to cut a house key for everyone who buys a home using us with a key that matches our logo. There's only one key shape that works really well, so that needs to match the logo in order for the idea to work. I'll attach an image of the key blank.... although the way the key hole cut out looks terrible, so I was thinking of having them just do a thin outline instead.
Would like a similar, matching logo for the Sunbrew Cafe... but possibly something that would be a little less formal and would be cute on a coffee mug- nothing stuffy.
AND, we're opening a home inspection company as well, and we would like that logo and branding to match. The home inspection company is "Bright Fern Home Inspections"
We were thinking that for the home inspection company , we could use a magnifying glass shape inside of the house shape for the logo, use a keyhole shape inside of the same house for the mortgage company, and use a coffee cup inside of the house shape for Sunbrew Cafe.
Just getting stuck and need to help. I designed the attached logo myself, and that is what we are currently using. Designers at local printing companies have failed to impress us.
The mortgage industry has a lot of numbers and logos, etc that they require us to put on our business cards... so it's hard to keep them looking clean.
HELP! HELP! :)

```html
<!DOCTYPE html>
<html lang="en">
<head>
<meta charset="utf-8">
<title>Bright Fern Mortgage Group – Business Card</title>
<link href="https://fonts.googleapis.com/css2?family=Marcellus&family=Alegreya:wght@700&family=Lato:wght@400&display=swap" rel="stylesheet">
<style>
  :root {
    --backdrop: #2f2f2f;
    --brand-blue: #236384;
    --ink-blue: #1f5a7e;
    --card-white: #ffffff;
    --card-offwhite: #f8f8f8;
    --text-dark: #222222;
  }
  html, body {
    margin: 0;
    padding: 0;
    width: 1200px;
    height: 900px;
    overflow: hidden;
    background: var(--backdrop);
  }
  .canvas {
    position: relative;
    width: 1200px;
    height: 900px;
  }
  .card {
    position: absolute;
    top: 306px;
    width: 440px;
    height: 271px;
    overflow: hidden;
  }
  .card-front {
    left: 149px;
    background: var(--card-white);
  }
  .card-back {
    left: 608px;
    background: var(--card-offwhite);
  }
  .brand-band {
    position: absolute;
    left: 0;
    top: 0;
    width: 100%;
    height: 118px;
    background: var(--brand-blue);
  }
  .wordmark {
    position: absolute;
    font-family: "Marcellus", serif;
    font-weight: 400;
    margin: 0;
    line-height: 1;
  }
  .wordmark span { display: block; }
  .wordmark .wordmark-main {
    font-size: 36px;
    letter-spacing: 0.5px;
    text-transform: uppercase;
  }
  .wordmark .wordmark-sub {
    font-size: 36px;
    margin-top: 4px;
  }
  .card-front .wordmark {
    left: 23px;
    top: 24px;
    color: var(--card-white);
  }
  .card-front .wordmark .wordmark-main,
  .card-front .wordmark .wordmark-sub { font-size: 32px; }
  .card-back .wordmark {
    left: 0;
    width: 100%;
    top: 98px;
    text-align: center;
    color: var(--ink-blue);
  }
  .card-back .wordmark .wordmark-main,
  .card-back .wordmark .wordmark-sub { font-size: 34px; }
  .person {
    position: absolute;
    left: 23px;
    top: 157px;
  }
  .person-name {
    margin: 0;
    font-family: "Alegreya", serif;
    font-weight: 700;
    font-size: 15px;
    letter-spacing: 0.6px;
    color: var(--ink-blue);
    line-height: 1;
  }
  .person-title {
    margin: 3px 0 0;
    font-family: "Lato", sans-serif;
    font-size: 12px;
    color: var(--text-dark);
  }
  .contact-list {
    position: absolute;
    left: 23px;
    top: 199px;
    margin: 0;
    padding: 0;
    list-style: none;
    font-family: "Lato", sans-serif;
    font-size: 12.5px;
    color: var(--text-dark);
  }
  .contact-list li {
    display: flex;
    align-items: center;
    height: 16px;
  }
  .contact-list svg {
    width: 9px;
    height: 9px;
    margin-right: 6px;
    fill: var(--ink-blue);
  }
  .address {
    position: absolute;
    right: 23px;
    top: 215px;
    margin: 0;
    font-family: "Lato", sans-serif;
    font-style: normal;
    font-size: 12.5px;
    line-height: 16px;
    text-align: right;
    color: var(--text-dark);
  }
</style>
</head>
<body>
<main class="canvas">
  <section class="card card-front">
    <div class="brand-band"></div>
    <h1 class="wordmark">
      <span class="wordmark-main">Bright Fern</span>
      <span class="wordmark-sub">Mortgage Group</span>
    </h1>
    <div class="person">
      <p class="person-name">DANIEL CARVER</p>
      <p class="person-title">Managing Director</p>
    </div>
    <ul class="contact-list">
      <li>
        <svg viewBox="0 0 10 10" aria-hidden="true"><path d="M2 0.5 L3.6 0.5 L4.2 3 L3 3.8 Q4 6 6.2 7 L7 5.8 L9.5 6.4 L9.5 8 Q9.5 9.5 8 9.5 Q0.5 9 0.5 2 Q0.5 0.5 2 0.5 Z"/></svg>
        (044)123456789
      </li>
      <li>
        <svg viewBox="0 0 10 10" aria-hidden="true"><path d="M0.5 2 H9.5 V8 H0.5 Z M0.5 2 L5 5.5 L9.5 2" fill="var(--ink-blue)"/><path d="M1 2.6 L5 5.6 L9 2.6" stroke="#fff" stroke-width="0.8" fill="none"/></svg>
        info@youremail.com
      </li>
      <li>
        <svg viewBox="0 0 10 10" aria-hidden="true"><circle cx="5" cy="5" r="4.5"/></svg>
        www.websitename.com
      </li>
    </ul>
    <address class="address">1234, Address GoesHere,<br>Country name, 12345</address>
  </section>

  <section class="card card-back">
    <h2 class="wordmark">
      <span class="wordmark-main">Bright Fern</span>
      <span class="wordmark-sub">Mortgage Group</span>
    </h2>
  </section>
</main>
</body>
</html>
```